HearthMile business card and stationary design

We are looking for a simple yet elegant design for our mortgage company business card and stationary.

The card should include:
Name (Marcus Pell)
Title (CEO)
Phone Number (732-555-0182)
Address (48 Birchwell Court, Suite 314, Hazlet, NJ 07730)
Email (email@hearthmile.example)
"NMLS" i.e. (NMLS 61947)
"Company NMLS" (Company NMLS 274615)

Contact Information for Business Card

See above

```html
<!DOCTYPE html>
<html lang="en">
<head>
<meta charset="utf-8">
<title>HearthMile Business Card</title>
<link rel="stylesheet" href="https://fonts.googleapis.com/css2?family=Arimo:wght@400;700&display=swap">
<style>
  :root {
    --navy: #1b2632;
    --sky: #27a9e1;
    --paper: #ffffff;
    --ink: #1f2328;
    --stage: #e7e9ec;
  }
  * { box-sizing: border-box; margin: 0; padding: 0; }
  html, body { width: 1200px; height: 912px; overflow: hidden; }
  body {
    background: var(--stage);
    font-family: "Arimo", Arial, sans-serif;
    position: relative;
  }
  .card {
    position: absolute;
    width: 640px;
    height: 366px;
    border-radius: 18px;
    overflow: hidden;
    box-shadow: 0 10px 26px rgba(20, 30, 40, 0.22);
  }
  .card-front { left: 200px; top: 60px; background: var(--navy); }
  .card-back  { left: 360px; top: 486px; background: var(--paper); }

  .brand {
    display: flex;
    align-items: center;
    gap: 12px;
    font-weight: 700;
    letter-spacing: -0.5px;
    white-space: nowrap;
  }
  .brand-mark { width: 14px; height: 14px; background: var(--sky); flex: none; }
  .card-front .brand {
    position: absolute; left: 0; right: 0; top: 150px;
    justify-content: center;
    font-size: 58px; line-height: 66px; color: var(--paper);
  }
  .card-front .brand-mark { width: 22px; height: 22px; }
  .card-back .brand {
    position: absolute; left: 54px; top: 70px;
    font-size: 42px; line-height: 50px; color: var(--navy);
  }

  .person { position: absolute; left: 88px; top: 176px; }
  .person-name {
    font-size: 22px; line-height: 26px; font-weight: 700; color: var(--sky);
    letter-spacing: 0.3px; text-transform: uppercase;
  }
  .person-title { font-size: 15px; line-height: 18px; color: var(--ink); margin-top: 4px; margin-left: 12px; }
  .rule {
    position: absolute; left: 148px; top: 214px;
    width: 456px; height: 1px; background: var(--navy);
  }

  .contact {
    position: absolute; left: 112px; top: 240px;
    list-style: none; font-size: 14px; color: var(--ink); line-height: 21px;
  }
  .contact li { display: flex; align-items: center; gap: 8px; white-space: nowrap; }
  .contact svg { width: 13px; height: 13px; fill: var(--sky); flex: none; }

  .address {
    position: absolute; right: 40px; top: 228px;
    font-size: 13.5px; line-height: 19px; color: var(--ink); text-align: right;
    white-space: nowrap;
  }

  .base-band {
    position: absolute; left: 0; right: 0; bottom: 0; height: 14px; background: var(--navy);
  }
  .nmls-tab {
    position: absolute; right: 0; bottom: 14px;
    width: 200px; height: 58px;
    background: var(--sky);
    border-top-left-radius: 40px;
    color: var(--paper); font-size: 14px;
    display: flex; align-items: center; justify-content: center;
    white-space: nowrap;
  }
</style>
</head>
<body>
  <section class="card card-front" aria-label="Business card front">
    <div class="brand"><span class="brand-mark"></span>HearthMile</div>
  </section>

  <section class="card card-back" aria-label="Business card back">
    <div class="brand"><span class="brand-mark"></span>HearthMile</div>

    <div class="person">
      <p class="person-name">Marcus Pell</p>
      <p class="person-title">CEO</p>
    </div>
    <div class="rule"></div>

    <ul class="contact">
      <li>NMLS 61947</li>
      <li>
        <svg viewBox="0 0 16 16" aria-hidden="true"><path d="M3.5 1h3l1.2 3.5-2 1.3a9 9 0 0 0 4.5 4.5l1.3-2L15 9.5v3c0 1-1 2-2 2C6.9 14.5 1.5 9.1 1.5 3c0-1 1-2 2-2z"/></svg>
        732-555-0182
      </li>
      <li>
        <svg viewBox="0 0 16 16" aria-hidden="true"><path d="M1 3h14v10H1z M1 3l7 5.5L15 3" fill="none" stroke="#27a9e1" stroke-width="1.8"/></svg>
        email@hearthmile.example
      </li>
      <li>
        <svg viewBox="0 0 16 16" aria-hidden="true"><circle cx="8" cy="8" r="6.5" fill="none" stroke="#27a9e1" stroke-width="1.6"/><path d="M1.5 8h13M8 1.5c-3 3.5-3 9.5 0 13M8 1.5c3 3.5 3 9.5 0 13" fill="none" stroke="#27a9e1" stroke-width="1.2"/></svg>
        www.hearthmile.example
      </li>
    </ul>

    <p class="address">48 Birchwell Court, Suite<br>314, Ashby Ridge, NJ 07791</p>

    <div class="nmls-tab">Company NMLS 274615</div>
    <div class="base-band"></div>
  </section>
</body>
</html>
```